Fine Art business needs new website

We need a simple website with a home page, about us page, New sculptures, Sold sculptures, and a contact us page.Our sculptures are very high end one of a kind pieces. As such we need the site to be VERY elegant and professional. Lastly, because I'll be updating pictures on the website on a monthly basis it needs to be user friendly to update (Wordpress is preferred). The only branding we have so far for the business is a business card.
Updates
I wasn't completely ready when this project launched, also I am on the road right now and haven't been able to be as responsive to all you designers as I would like. I will work on giving feedback to all the top designs we've received so far. Thank you all so much for your participation and hardwork.
Target Market(s)
High end customers (affluent), art collectors, interior decorators/designers
Industry/Entity Type
Art Gallery
Coding
Coded - Design and coding required
Number of Pages Required
5+ page
Requirements
Must have
- Easily editable picture gallery for myself so that I can add new pieces(pictures of the pieces), remove sold pieces, etc. I would like the website to be built in wordpress so I can update it. I currently use mangewordpress through Netmarro for my other business website and would like to do the same for this one.
- Pages:
- -Intro page with featured pieces
- -Current pieces gallery (for sale) mainly a picture gallery
- -Sculptures archive (sold pieces) another picture gallery
- -About us: Pull-down of -about the artist (attached content)
- -Artistic Process (attached content)
- -Show Schedule:
- -one page dedicated to "friends of TMV" (basically a link page)
- TO BE CLEAR "www.pineroverslane.com" IS A TOTALLY DIFFERENT SITE AND I'M NOT TRYING TO COMBINE THE TWO OR JOIN THEM INTO ONE. This page needs be more elegant and seperate from the Pine Rovers site.
- UPDATE: I'd like a link to the TMV Facebook page: https://www.faceplume-social.com/mirelcraftworks/
Nice to have
- I would like the pictures on the gallery pages able to have text connected with them (Materials, price)
- I would like the site style and fonts to be similar to our business cards we've already had designed (picture attached).
Should not have
- Too much flash or other things that will make the site slow to load.

```html
<!DOCTYPE html>
<html lang="en">
<head>
<meta charset="utf-8">
<title>Mirel Craftworks — About the Artists</title>
<link rel="stylesheet" href="https://fonts.googleapis.com/css2?family=Lato:wght@400;700;900&family=Lora:ital,wght@0,700;1,400&display=swap">
<style>
:root{
  --ink:#2b2b2b;
  --body:#4a4a4a;
  --nav:#1f1f1f;
  --footer:#1c1c1c;
  --band:#f1f1f1;
  --paper:#ffffff;
  --rule:#3a3a3a;
  --social:#2f8fd6;
  --logo:#5b4a7a;
}
*{box-sizing:border-box;margin:0;padding:0}
html,body{width:1200px;height:4932px;overflow:hidden}
body{position:relative;background:var(--paper);font-family:"Lato",sans-serif;color:var(--body)}
.abs{position:absolute}

/* navigation */
.site-nav{left:0;top:0;width:1200px;height:66px;background:var(--nav)}
.nav-links{left:187px;top:0;height:66px;display:flex;align-items:center;gap:26px;list-style:none}
.nav-links li{color:#fff;font-size:15px;font-weight:700;letter-spacing:.5px}
.nav-dropdown{left:200px;top:56px;width:130px;background:#fff;box-shadow:0 2px 6px rgba(0,0,0,.25);padding:6px 0}
.nav-dropdown li{list-style:none;font-size:12px;font-weight:700;color:var(--ink);padding:6px 12px}
.nav-dropdown li:first-child{background:#222;color:#fff;margin:0 6px}
.menu-toggle{right:190px;top:22px}

/* headings */
.section-title{left:0;width:1200px;text-align:center;font-size:31px;font-weight:900;color:var(--ink);letter-spacing:.5px}
.section-title::after{content:"";display:block;width:70px;height:2px;background:var(--rule);margin:10px auto 0}

/* logo */
.brand{left:0;top:170px;width:1200px;text-align:center}
.brand-name{font-size:58px;font-weight:400;color:var(--logo);letter-spacing:8px;line-height:76px;text-transform:uppercase}

/* media placeholders */
.media{border-radius:2px;box-shadow:0 2px 6px rgba(0,0,0,.25)}

.prose{left:329px;width:552px;text-align:center;font-size:15px;line-height:24px;color:var(--body)}
.prose p{margin-bottom:18px}

/* artists band */
.artists-band{left:0;top:1282px;width:1200px;height:559px;background:var(--band)}
.artist-name{font-size:22px;font-weight:700;color:var(--ink)}
.bio{width:360px;font-family:"Lora",serif}
.bio h3{font-size:15px;font-weight:700;color:var(--ink);margin-bottom:10px}
.bio p{font-size:15px;font-style:italic;line-height:22px;color:#555}

/* finishing band */
.finish-band{left:0;top:4274px;width:1200px;height:451px;background:var(--band)}

/* footer */
.site-footer{left:0;top:4725px;width:1200px;height:207px;background:var(--footer);color:#fff}
.foot-col{top:42px}
.foot-col h4{font-size:22px;font-weight:900;letter-spacing:.5px;margin-bottom:10px}
.foot-col p,.foot-col li{font-size:12px;font-weight:700;line-height:19px;list-style:none}
.contact-line{display:flex;align-items:center;gap:8px}
.social{display:flex;gap:8px;margin-top:4px;justify-content:center}
.social span{width:20px;height:20px;background:var(--social);border-radius:2px}
</style>
</head>
<body>

<nav class="site-nav abs">
  <ul class="nav-links abs">
    <li>HOME</li><li>ABOUT ▾</li><li>GALLERY</li><li>CONTACT</li>
  </ul>
  <svg class="menu-toggle abs" width="36" height="22" viewBox="0 0 36 22"><rect y="0" width="36" height="3" fill="#fff"/><rect y="9" width="36" height="3" fill="#fff"/><rect y="18" width="36" height="3" fill="#fff"/></svg>
</nav>
<ul class="nav-dropdown abs">
  <li>About the Artists</li>
  <li>The Pine Rovers</li>
</ul>

<header class="brand abs">
  <div class="brand-name">Mirel<br>Craftworks</div>
</header>

<h2 class="section-title abs" style="top:432px">MEET THE ARTISTS</h2>
<div class="media abs" role="img" aria-label="Photo of the two artists in protective masks in the workshop" style="left:418px;top:520px;width:371px;height:280px;background:linear-gradient(135deg,#8a6a4c,#c9b79a 55%,#6e7f8c)"></div>

<div class="prose abs" style="top:832px">
  <p>Rue Halvorsen has been mastering the Lapidary Arts since the late 1980's. Somewhere in the middle of this new career of his he recruited his kids into the shop to help him with the ever increasing demand for his one of a kind fossil and mineral sculptures. An unintended (or possibly intended) consequence of bringing his children into the fold is they eventually fell in love with rocks and became proficient in many of the lapidary techniques.</p>
  <p>Fast forward to 2012, after graduating college and working several years in the real world two of Rue's children, Dorian and Sela, decided to work with their Father full-time as a chance to be closer to family while at the same time seeing different parts of the US. Through the past 6 years all of Rue's children have continued to contribute to the family livelihood on a part-time basis with the exception of Dory who is now a full time Artist alongside his Father.</p>
  <p>Both Rue and Dory have their own unique styles, yet on occasion they will combine their talents to create a collaborative masterpiece.</p>
</div>

<section class="artists-band abs"></section>
<div class="artist-name abs" style="left:99px;top:1325px">Richard “Rue” Halvorsen</div>
<div class="media abs" role="img" aria-label="Portrait of Rue Halvorsen outdoors" style="left:191px;top:1364px;width:279px;height:208px;background:linear-gradient(135deg,#7a5a40,#b39a7c 50%,#5c6b4e)"></div>
<div class="bio abs" style="left:493px;top:1418px">
  <h3>Biography</h3>
  <p>“To learn more about the process of creating these one-of-a-kind sculptures please visit the Artistic process page of the website.”</p>
</div>

<div class="artist-name abs" style="right:95px;top:1566px">Dory Halvorsen</div>
<div class="bio abs" style="left:263px;top:1671px;text-align:right">
  <h3 style="text-align:left">Biography</h3>
  <p>“To learn more about the process of creating these one-of-a-kind sculptures please visit the Artistic process page of the website.”</p>
</div>
<div class="media abs" role="img" aria-label="Portrait of Dory Halvorsen in a snowy yard" style="left:740px;top:1621px;width:273px;height:187px;background:linear-gradient(135deg,#cfd6dc,#8c8074 55%,#4f5a63)"></div>

<h2 class="section-title abs" style="top:1885px">ARTISTIC PROCESS</h2>

<div class="prose abs" style="top:1963px">
  <p>Picking out the Rough- The entire artistic process begins with the difficult task of being able to see the potential inside a rough un-finished stone. One would be quite amazed at the incredible difference between a completely rough specimen and the finished product (see photos below).</p>
  <p>Secondly, a trained lapidary artist must be familiar with the physical attributes of each stone he works with. This includes know how hard each mineral is, what their fracture points are, how they polish up, and most importantly which tools needed to work said minerals.</p>
  <p>The last part of picking out the rough is knowing where to find the most unique and rare specimens which in most cases requires building relationships with the miners of the different countries in which the materials are found.</p>
</div>
<div class="media abs" role="img" aria-label="Rough geode specimen held in hand" style="left:418px;top:2279px;width:174px;height:243px;background:linear-gradient(160deg,#7c7366,#c9b48e 50%,#5f574c)"></div>
<div class="media abs" role="img" aria-label="Cut geode showing crystal interior" style="left:608px;top:2279px;width:175px;height:243px;background:linear-gradient(160deg,#6a6154,#e2cf9e 50%,#7a6a52)"></div>

<div class="prose abs" style="top:2581px">
  <p>Shaping the stone- Most work on shaping a fossil or mineral is done outside, full protected, with a right angle grinder and a diamond cup-wheel or blade. Though on some occasions we'll use a wet slab-saw to cut pieces that need a flat surface.</p>
  <p>However, all contoured surfaces must be done by hand with a right angle grinder or air powered die grinder. This is typically the most labor intensive part in creating a sculpture.</p>
</div>
<div class="media abs" role="img" aria-label="Shaped stone sculpture in the workshop" style="left:450px;top:2778px;width:142px;height:240px;background:linear-gradient(160deg,#8b7a64,#d8c8a8 50%,#6b5d4c)"></div>
<div class="media abs" role="img" aria-label="Close view of a shaped crystal piece" style="left:608px;top:2778px;width:138px;height:240px;background:linear-gradient(160deg,#a08c6c,#efe2c0 50%,#8a7454)"></div>

<div class="prose abs" style="top:3074px">
  <p>Polishing the stone- After we are satisfied with the shape of the sculpture it's time to bring it into the wet room. In the wet room we use a similar variable speed right angle grinder with the added feature of an attached water-feed.</p>
  <p>The water is for two main reasons, to keep the dust down, and to prolong the life of the very expensive diamond pads. The typical process of polishing a stone will be to start with a 30 grit diamond pad followed consecutively by 50 grit, 100 grit, 200 grit, 400 grit, 800 grit, 1500 grit, 3000 grit, 5000 grit, 10000 grit, and finally a softer polishing pad. This step of the process usually takes 10-15 hours in the wet-room.</p>
</div>
<div class="media abs" role="img" aria-label="Set of colored diamond polishing pads" style="left:404px;top:3341px;width:188px;height:187px;background:linear-gradient(90deg,#3c5a9a,#2f8a4a 25%,#c8b23a 50%,#c0392b 75%,#2b2b2b)"></div>
<div class="media abs" role="img" aria-label="Artist polishing a stone in the wet room" style="left:608px;top:3341px;width:188px;height:187px;background:linear-gradient(160deg,#7e8a92,#c4c8c6 50%,#5b636a)"></div>

<div class="prose abs" style="top:3567px">
  <p>Balancing and drilling- Once the we've finished the shaping and polishing of both parts of the sculpture we must now figure out how the two pieces will combine together. Anyone who has seen our sculptures before knows that our hallmark trait is to make each piece balance perfectly so it spins freely. Because this feature is often copied in the sculpture world I won't go into too much detail as to how we find the exact center of balance.</p>
  <p>Measurements and adjustments at this point in the process must be precise. Once the center of gravity is found the piece must be jigged up, flipped 180 degrees, and drilled (wet) precisely in the same orientation. This portion of the creation process can be one of the most stress-inducing for the simple reason that an error at this point can ruin the entire piece (and has before).</p>
</div>
<div class="media abs" role="img" aria-label="Polished crystal piece on a workbench" style="left:404px;top:3962px;width:89px;height:164px;background:linear-gradient(160deg,#b08a3c,#ecd28a 50%,#6b5630)"></div>
<div class="media abs" role="img" aria-label="Artist drilling a sculpture at the press" style="left:510px;top:3880px;width:82px;height:246px;background:linear-gradient(160deg,#9a5c4a,#d4c4b0 50%,#4e5660)"></div>
<div class="media abs" role="img" aria-label="Sculpture halves set up for balancing" style="left:602px;top:3962px;width:194px;height:164px;background:linear-gradient(160deg,#6f6a62,#c8bba4 50%,#4a4640)"></div>

<div class="prose abs" style="top:4159px">
  <p>Finishing touches- Once all the above has been achieved the final touches include cutting pins and sleeves to fit the two pieces together perfectly and cleaning each piece so it's ready to be shown to the public</p>
</div>

<section class="finish-band abs"></section>
<h2 class="section-title abs" style="top:4341px;font-size:24px">FINISHING PRODUCT</h2>
<div class="media abs" role="img" aria-label="Finished balanced stone sculpture" style="left:516px;top:4412px;width:174px;height:240px;background:linear-gradient(160deg,#5a6a7a,#c9b48a 50%,#3e4652)"></div>

<footer class="site-footer abs">
  <div class="foot-col abs" style="left:197px;width:150px">
    <h4>ABOUT US</h4>
    <p>This is a dummy text just to provide text in the About Us section which will be added correctly later on.</p>
  </div>
  <div class="foot-col abs" style="left:526px;width:200px">
    <h4>OUR ADDRESS</h4>
    <ul>
      <li class="contact-line"><svg width="11" height="11" viewBox="0 0 24 24"><path fill="#fff" d="M6.6 10.8a15 15 0 006.6 6.6l2.2-2.2c.3-.3.7-.4 1-.2 1.1.4 2.3.6 3.6.6.6 0 1 .4 1 1V20c0 .6-.4 1-1 1A17 17 0 013 4c0-.6.4-1 1-1h3.5c.6 0 1 .4 1 1 0 1.3.2 2.5.6 3.6.1.3 0 .7-.2 1z"/></svg>(555) 014-2290</li>
      <li class="contact-line"><svg width="11" height="11" viewBox="0 0 24 24"><rect x="2" y="5" width="20" height="14" fill="none" stroke="#fff" stroke-width="2"/><path d="M2 5l10 8 10-8" fill="none" stroke="#fff" stroke-width="2"/></svg>dory@pineroverslane.com</li>
      <li class="contact-line"><svg width="11" height="11" viewBox="0 0 24 24"><circle cx="12" cy="12" r="9" fill="none" stroke="#fff" stroke-width="2"/><path d="M3 12h18M12 3c3 3 3 15 0 18M12 3c-3 3-3 15 0 18" fill="none" stroke="#fff" stroke-width="1.5"/></svg>www.mirelcraftworks.com</li>
      <li style="padding-left:19px">CONTACT US</li>
    </ul>
  </div>
  <div class="foot-col abs" style="left:820px;width:200px;text-align:center">
    <h4>KEEP IN TOUCH</h4>
    <div class="social"><span></span><span></span><span></span><span></span></div>
  </div>
</footer>

</body>
</html>
```